GJ & DW Fencing Pty Ltd

We already have an existing logo created by Pixel Harbour however we have restructured to a company. We would like someone to add Pty Ltd to our business name please.

Colors

Designer to choose only greyscale colors for use in the design.

```html
<!DOCTYPE html>
<html lang="en">
<head>
<meta charset="utf-8">
<title>GJ &amp; DW Fencing Pty Ltd – Business Card</title>
<link href="https://fonts.googleapis.com/css2?family=Merriweather:wght@400&family=Lato:wght@400&display=swap" rel="stylesheet">
<style>
  :root {
    --page-bg: #d9d9d9;
    --card-front: #1e1e1e;
    --card-back: #0d0d0d;
    --ink-light: #f2f2f2;
    --ink-soft: #e6e6e6;
    --art-tone: #f4f4f4;
  }
  html, body {
    margin: 0;
    padding: 0;
    width: 1200px;
    height: 802px;
    overflow: hidden;
    background: var(--page-bg);
  }
  .canvas {
    position: relative;
    width: 1200px;
    height: 802px;
  }
  .card {
    position: absolute;
    top: 274px;
    width: 443px;
    height: 265px;
    overflow: hidden;
  }
  .card--front { left: 136px; background: var(--card-front); }
  .card--back  { left: 624px; background: var(--card-back); }

  .card__art {
    position: absolute;
    left: 0;
    top: 12px;
    width: 205px;
    height: 253px;
    background: linear-gradient(180deg, var(--art-tone) 0%, #e9e9e9 100%);
  }

  .card__names {
    position: absolute;
    left: 224px;
    top: 72px;
    margin: 0;
    font-family: "Merriweather", Georgia, serif;
    font-weight: 400;
    font-size: 15.5px;
    line-height: 24px;
    letter-spacing: 0.4px;
    color: var(--ink-light);
    text-transform: uppercase;
  }

  .contact {
    position: absolute;
    left: 223px;
    top: 137px;
    margin: 0;
    padding: 0;
    list-style: none;
    font-family: "Lato", Arial, sans-serif;
    font-size: 12.5px;
    line-height: 15px;
    color: var(--ink-soft);
  }
  .contact__item {
    display: flex;
    align-items: flex-start;
    gap: 6px;
    margin-bottom: 5px;
  }
  .contact__icon {
    flex: none;
    width: 15px;
    height: 15px;
  }

  .wordmark {
    position: absolute;
    left: 0;
    right: 0;
    top: 95px;
    text-align: center;
    font-family: "Merriweather", Georgia, serif;
    font-weight: 400;
    color: var(--ink-light);
  }
  .wordmark__name {
    display: block;
    font-size: 38px;
    line-height: 44px;
  }
  .wordmark__sub {
    display: block;
    font-size: 14px;
    line-height: 22px;
    letter-spacing: 2px;
    text-transform: uppercase;
  }
</style>
</head>
<body>
<main class="canvas">
  <section class="card card--front">
    <div class="card__art" role="img" aria-label="Illustration of a standing white farm animal"></div>
    <p class="card__names">Glen Jarvis &amp;<br>Dana Whitlock</p>
    <ul class="contact">
      <li class="contact__item">
        <svg class="contact__icon" viewBox="0 0 16 16" aria-hidden="true">
          <circle cx="8" cy="8" r="8" fill="#f2f2f2"/>
          <path d="M5 5.5h6v1.2H5zM6 7.5h4l0.8 3H5.2z" fill="#1e1e1e"/>
        </svg>
        <span>041 5528190</span>
      </li>
      <li class="contact__item">
        <svg class="contact__icon" viewBox="0 0 16 16" aria-hidden="true">
          <circle cx="8" cy="8" r="8" fill="#f2f2f2"/>
          <rect x="4.2" y="5.2" width="7.6" height="5.6" fill="none" stroke="#1e1e1e" stroke-width="1.1"/>
          <path d="M4.2 5.4 8 8.4l3.8-3" fill="none" stroke="#1e1e1e" stroke-width="1.1"/>
        </svg>
        <span>gjdwfencing@mailbox.com</span>
      </li>
      <li class="contact__item">
        <svg class="contact__icon" viewBox="0 0 16 16" aria-hidden="true">
          <circle cx="8" cy="8" r="8" fill="#f2f2f2"/>
          <path d="M8 3.5a3 3 0 0 1 3 3c0 2.2-3 5.8-3 5.8S5 8.7 5 6.5a3 3 0 0 1 3-3z" fill="#1e1e1e"/>
          <circle cx="8" cy="6.5" r="1.1" fill="#f2f2f2"/>
        </svg>
        <span>PO Box 418 Merredin<br>WA 6415</span>
      </li>
    </ul>
  </section>

  <section class="card card--back">
    <div class="wordmark">
      <span class="wordmark__name">GJ &amp; DW</span>
      <span class="wordmark__sub">Fencing Pty Ltd</span>
    </div>
  </section>
</main>
</body>
</html>
```